Linkbook & Instagram Design for: The Ledger of Pim - Paws of Quiet Hound

Need a Linkbook Page and Instagram Page too for helping launch a book as a brand new author with a book on my old dog Pim and the Zen lessons he taught me.
Its all for folks who love dogs and especially rescue dog stories
Its all for folks who are interested in something slightly spiritual and for self growth
I attach the review copy from my publishers who are standing up a website but recommend a Linkbook Page that is attached to my own personal one and an Instagram Page
I intend on publishing weekly "Pimtricks" (The dog was called Pim)
I intend on posting Zen talks (in lay man's terms)
I have a second book being written to follow on the one
Myself as an Author needs profiling
The book needs ALOT of promotion - and we can't travel!
I need to host a bunch of "book talks/launches"
Need to send folks to my website to by the book: Hard/Paperback/Lumera - which comes with book trailer
I have hundreds of photos to give
I have alot of sketches of the dog to share which did not make it into the book
My competition are books like:
Hollis & Us
A Cat naps int Caring Lodge
Tuxa
The Baron's Beagle
A Pups Journey
Need this ASAP - publishing date is moved up to October 2021!
Link t Author hot File Crate: https://www.filecrate.example/sh/kqwplm2231907t4/AAFhtrWmnPqLsKe7vb_XoPla?dl=0
Link to Dog Photos:
https://www.filecrate.example/sh/mvbtr83knwoz02/AAC4j1hnqe_k5Rs9WYpoltQ2m?dl=0
Updates
Hello, I will be in hospitaal having surgery on my neck and request tow more days to =make any kind of small changes. Thank you Marisol
Target Market(s)
Dog owners around the world, especially those wth rescue dogs and those looking for personal growth and those interested in Zen Buddhism
Industry/Entity Type
Author promoting soon to be published book/s
Requirements
Must have
- Author Photo/E-Mail Sign Up/Link to Instagram (see brief to design this)/Link to upcoming website/Link to Writer Hub (might need to design me something)/Photo Gallery
Nice to have
- Author features and Dog Images (I have new dogs we can show)
Should not have
- Cute - its a meaningful book

```html
<!DOCTYPE html>
<html lang="en">
<head>
<meta charset="utf-8">
<title>The Ledger of Pim – Linkbook Page Presentation</title>
<link rel="stylesheet" href="https://fonts.googleapis.com/css2?family=Montserrat:wght@500;700&family=Roboto:wght@400;500;700&family=Kaushan+Script&family=Great+Vibes&display=swap">
<style>
:root{
  --canvas:#eceef1;
  --white:#ffffff;
  --annot:#1f55c9;
  --fb-blue:#1877f2;
  --text:#1c1e21;
  --muted:#65676b;
  --line:#dadde1;
  --btn:#e4e6eb;
  --notice:#8c8c8c;
  --title-teal:#1a8fc9;
  --band:#4a4ec8;
  --cover-sky-a:#d7e3f1;
  --cover-sky-b:#9fb4d8;
  --cover-coat:#b0304f;
  --photo-dark:#4a4746;
  --photo-warm:#8a6a50;
}
*{box-sizing:border-box;margin:0;padding:0}
html,body{width:1200px;height:1200px;overflow:hidden}
body{background:var(--canvas);font-family:Roboto,Arial,sans-serif;color:var(--text);position:relative}
.abs{position:absolute}

/* annotations */
.side-label{position:absolute;font-family:Montserrat,Arial,sans-serif;color:var(--annot);font-weight:500;white-space:nowrap;transform-origin:left top;transform:rotate(-90deg)}
.side-label-cover{left:36px;top:366px;font-size:30px;letter-spacing:1px}
.side-label-admin{left:58px;top:1115px;font-size:50px}
.callout{position:absolute;font-family:Montserrat,Arial,sans-serif;color:var(--annot);font-weight:500;text-align:center;line-height:1.16}
.callout.shop{left:1000px;top:570px;width:160px;font-size:22px}
.callout.photo{left:990px;top:920px;width:180px;font-size:26px;line-height:1.1}
.pointer{position:absolute;left:970px;width:120px;height:140px}

/* cover */
.cover-art{left:121px;top:29px;width:996px;height:369px;overflow:hidden;background:linear-gradient(180deg,var(--cover-sky-b) 0%,var(--cover-sky-a) 55%,#eef2f7 100%)}
.cover-photo{position:absolute;left:0;top:0;width:560px;height:369px;background:radial-gradient(ellipse at 35% 45%,#c98c73 0%,var(--cover-coat) 40%,#6b5b66 75%,rgba(120,120,150,0) 100%)}
.cover-title{position:absolute;left:500px;top:52px;width:480px;text-align:center;font-family:Montserrat,Arial,sans-serif;font-weight:700;font-size:38px;color:var(--title-teal);white-space:nowrap;letter-spacing:1px}
.cover-sub{position:absolute;left:500px;top:120px;width:480px;text-align:center;font-family:'Kaushan Script',cursive;font-size:40px;color:#263247;white-space:nowrap}
.cover-quote{position:absolute;left:530px;top:196px;width:420px;font-family:Montserrat,Arial,sans-serif;font-weight:700;font-size:18px;line-height:28px;color:#4a4f86;text-align:center;text-transform:uppercase}
.cover-soon{position:absolute;left:50px;top:240px;font-family:'Great Vibes',cursive;font-size:80px;color:var(--white);white-space:nowrap}
.cover-band{position:absolute;left:451px;top:293px;width:545px;height:46px;background:var(--band);display:flex;align-items:center;justify-content:space-around;padding:0 10px}
.cover-band span{font-family:Montserrat,Arial,sans-serif;font-weight:500;font-size:16px;color:var(--white);white-space:nowrap}

/* notice bar */
.notice{left:0;top:398px;width:1200px;height:46px;background:var(--notice);display:flex;align-items:center;padding-left:14px;color:var(--white);font-size:12.5px;font-weight:500;z-index:2}
.notice svg{margin-right:10px}
.publish{left:1083px;top:406px;width:117px;height:28px;background:var(--fb-blue);color:var(--white);font-weight:700;font-size:12.5px;border-radius:5px 0 0 5px;display:flex;align-items:center;justify-content:center;z-index:3}

/* header */
.header{left:0;top:444px;width:1200px;height:121px;background:var(--white);border-bottom:1px solid var(--line)}
.avatar{left:265px;top:396px;width:106px;height:106px;border-radius:50%;background:var(--white);border:3px solid #f2f2f2;display:flex;align-items:center;justify-content:center;flex-direction:column;font-weight:500;color:var(--text);z-index:1}
.avatar .mark{width:26px;height:26px;border-radius:50%;background:#c9d3e2;margin:14px 0 4px}
.avatar .name{font-size:15px;line-height:1}
.cam{left:343px;top:474px;width:28px;height:28px;border-radius:50%;background:var(--btn);display:flex;align-items:center;justify-content:center;z-index:1}
.page-name{left:394px;top:448px;font-size:21px;font-weight:700}
.page-handle{left:394px;top:476px;font-size:13.5px;color:var(--muted)}
.page-handle b{color:var(--fb-blue);font-weight:500}
.btn{position:absolute;display:flex;align-items:center;justify-content:center;border-radius:5px;font-size:13px;font-weight:500;gap:6px}
.btn.grey{background:var(--btn);color:var(--text)}
.btn.blue{background:var(--fb-blue);color:var(--white)}
.edit-shop{left:714px;top:462px;width:248px;height:32px}
.header-rule{left:262px;top:516px;width:700px;height:1px;background:var(--line)}
.tabs{left:262px;top:531px;display:flex;font-size:12.5px;color:var(--muted);font-weight:500}
.tabs span{padding:0 13px;height:31px}
.tabs .active{color:var(--fb-blue);border-bottom:3px solid var(--fb-blue)}
.promote{left:745px;top:526px;width:128px;height:28px}
.icon-btn{width:38px;height:28px;top:526px}

/* feed cards */
.card{position:absolute;background:var(--white);border-radius:7px;box-shadow:0 1px 2px rgba(0,0,0,.12)}
.setup{left:262px;top:578px;width:288px;height:302px;padding:13px}
.card h3{font-size:15.5px;font-weight:700;margin-bottom:5px}
.setup p{font-size:13px;line-height:16px;color:#3a3b3c}
.steps{font-size:10.5px;color:var(--muted);margin-top:6px}
.progress{display:flex;gap:4px;margin-top:5px}
.progress i{width:16px;height:6px;border-radius:3px;background:var(--btn)}
.progress i.on{background:var(--fb-blue)}
.step-row{border-top:1px solid #ccd0d5;margin-top:14px;padding-top:14px;position:relative;height:54px}
.step-row + .step-row{margin-top:0}
.step-row small{display:block;font-size:10.5px;color:var(--muted)}
.step-row strong{display:block;font-size:13px;font-weight:500;margin-top:3px}
.step-row svg{position:absolute;right:8px;top:20px}
.tools{left:262px;top:894px;width:288px;height:176px;padding:13px}
.tool{display:flex;gap:12px;margin-top:14px;position:relative;padding-right:18px}
.tool .ic{width:24px;height:22px;border-radius:4px;flex:none;margin-top:2px}
.tool b{font-size:13px;font-weight:500}
.tool p{font-size:11.5px;line-height:15px;color:#3a3b3c}
.tool svg{position:absolute;right:4px;top:10px}
.insights{left:262px;top:1083px;width:288px;height:60px;padding:10px 13px;display:flex;justify-content:space-between}
.insights a{font-size:12px;color:var(--fb-blue);text-decoration:none;margin-top:4px}
.create-post{left:563px;top:578px;width:399px;height:92px;padding:9px}
.mini-avatar{width:32px;height:32px;border-radius:50%;border:1px solid var(--line);display:flex;align-items:center;justify-content:center;font-weight:500;font-size:9px;color:var(--text)}
.cp-field{position:absolute;left:51px;top:9px;width:339px;height:32px;background:var(--btn);border-radius:5px;display:flex;align-items:center;justify-content:center;font-size:13px;font-weight:500}
.cp-actions{position:absolute;left:28px;top:58px;right:12px;display:flex;justify-content:space-between;font-size:12.5px;color:var(--muted);font-weight:500}
.cp-actions span{display:flex;align-items:center;gap:6px}
.create-bar{left:563px;top:683px;width:399px;height:53px;display:flex;align-items:center;padding-left:12px;gap:6px;font-size:12px;color:#3a3b3c}
.chip{background:#eef0f3;border-radius:16px;height:29px;padding:0 10px;display:flex;align-items:center;gap:5px;color:var(--text)}
.section-label{left:563px;top:762px;font-size:12px;color:var(--muted)}
.post{left:563px;top:788px;width:399px;height:345px;overflow:hidden}
.post-head{position:absolute;left:13px;top:9px;display:flex;gap:8px}
.post-head b{display:block;font-size:12px;font-weight:500}
.post-head small{font-size:10.5px;color:var(--muted)}
.post-photo{position:absolute;left:0;top:47px;width:399px;height:266px;background:radial-gradient(ellipse at 65% 45%,#a58a74 0%,var(--photo-warm) 22%,var(--photo-dark) 60%,#3c3a3a 100%)}
.post-foot{position:absolute;left:12px;top:322px;width:375px;display:flex;font-size:11.5px;color:#3a3b3c}
.post-foot .boost{margin-left:auto;background:var(--btn);border-radius:5px;padding:3px 10px;color:var(--muted);font-size:10px}
.fab{left:1180px;top:1075px;width:40px;height:40px;border-radius:50%;background:var(--white);box-shadow:0 1px 4px rgba(0,0,0,.2)}
</style>
</head>
<body>

<div class="side-label side-label-cover">COVER LINKBOOK</div>

<!-- cover -->
<section class="abs cover-art">
  <div class="cover-photo" role="img" aria-label="Author in a crimson coat smiling beside her brindle rescue dog"></div>
  <div class="cover-title">THE LEDGER OF PIM</div>
  <div class="cover-sub">Paws of Quiet Hound</div>
  <div class="cover-quote">“ All true stories of a rescue dog teaching his owner the real meaning of zen ”</div>
  <div class="cover-soon">Coming Soon</div>
  <div class="cover-band">
    <span>Riverstall Writer Hub</span><span>Pagewell</span><span>Harrow &amp; Finch</span><span>Stillbrook</span>
  </div>
</section>

<!-- page header -->
<div class="abs header"></div>
<div class="abs avatar" role="img" aria-label="Book emblem for The Ledger of Pim"><span class="mark"></span><span class="name">Pim</span></div>
<div class="abs notice">
  <svg width="20" height="14" viewBox="0 0 20 14"><ellipse cx="10" cy="7" rx="9" ry="6" fill="none" stroke="#fff" stroke-width="1.6"/><circle cx="10" cy="7" r="2.5" fill="#fff"/><line x1="3" y1="13" x2="17" y2="1" stroke="#fff" stroke-width="1.6"/></svg>
  This Page isn't visible. You can publish it when you're ready for people to see it.
</div>
<div class="abs publish">Publish Page</div>

<div class="abs cam"><svg width="14" height="12" viewBox="0 0 14 12"><rect x="0" y="2" width="14" height="10" rx="2" fill="#1c1e21"/><rect x="4" y="0" width="6" height="3" rx="1" fill="#1c1e21"/><circle cx="7" cy="7" r="2.6" fill="#e4e6eb"/></svg></div>
<div class="abs page-name">Test2</div>
<div class="abs page-handle"><b>Create @username</b> · Book</div>
<div class="btn grey edit-shop"><svg width="12" height="12" viewBox="0 0 12 12"><path d="M1 11l1-3 6-6 2 2-6 6z" fill="#1c1e21"/></svg>Edit Shop on Website</div>

<svg class="pointer" style="top:462px" viewBox="0 0 120 140"><polygon points="0,16 16,7 16,25" fill="var(--annot)"/><polygon points="40,16 56,7 56,25" fill="var(--annot)"/><polygon points="70,16 86,7 86,25" fill="var(--annot)"/><polyline points="86,16 110,16 110,100" fill="none" stroke="var(--annot)" stroke-width="1.6"/></svg>
<div class="callout shop">SHOP<br>button<br>for<br>redirection</div>

<div class="abs header-rule"></div>
<nav class="abs tabs"><span class="active">Home</span><span>About</span><span>Events</span><span>Reviews</span><span>More ▾</span></nav>
<div class="btn blue promote"><svg width="16" height="12" viewBox="0 0 16 12"><path d="M1 4h3l8-4v12L4 8H1z" fill="#fff"/></svg>Promote</div>
<div class="btn grey icon-btn" style="left:880px"><svg width="14" height="14" viewBox="0 0 14 14"><circle cx="6" cy="6" r="4.5" fill="none" stroke="#1c1e21" stroke-width="1.8"/><line x1="9.5" y1="9.5" x2="13" y2="13" stroke="#1c1e21" stroke-width="1.8"/></svg></div>
<div class="btn grey icon-btn" style="left:925px;font-weight:700">···</div>

<div class="side-label side-label-admin">Page from admin view</div>

<!-- left column -->
<section class="card setup">
  <h3>Set your Page up for success</h3>
  <p>Finish setting up your Page so people on Linkbook know that you're a credible business.</p>
  <div class="steps">8 of 13 steps completed</div>
  <div class="progress"><i class="on"></i><i class="on"></i><i class="on"></i><i class="on"></i><i class="on"></i><i class="on"></i><i class="on"></i><i class="on"></i><i></i><i></i><i></i><i></i><i></i></div>
  <div class="step-row"><small>Completed</small><strong>Establish your Page's identity</strong><svg width="10" height="6" viewBox="0 0 10 6"><polyline points="1,1 5,5 9,1" fill="none" stroke="#1c1e21" stroke-width="1.8"/></svg></div>
  <div class="step-row"><small>4 steps left</small><strong>Provide info and preferences</strong><svg width="10" height="6" viewBox="0 0 10 6"><polyline points="1,1 5,5 9,1" fill="none" stroke="#1c1e21" stroke-width="1.8"/></svg></div>
  <div class="step-row"><small>1 step left</small><strong>Introduce your Page</strong><svg width="10" height="6" viewBox="0 0 10 6"><polyline points="1,1 5,5 9,1" fill="none" stroke="#1c1e21" stroke-width="1.8"/></svg></div>
</section>

<section class="card tools">
  <h3>Free Linkbook Business tools</h3>
  <div class="tool"><span class="ic" style="background:#f3425f"></span><div><b>Add Appointment Bookings</b><p>Display your services and availability so that people can book an...</p></div><svg width="7" height="12" viewBox="0 0 7 12"><polyline points="1,1 6,6 1,11" fill="none" stroke="#65676b" stroke-width="1.4"/></svg></div>
  <div class="tool"><span class="ic" style="background:#f7923b"></span><div><b>Post a job</b><p>Find qualified candidates by posting job opportunities with your busine...</p></div><svg width="7" height="12" viewBox="0 0 7 12"><polyline points="1,1 6,6 1,11" fill="none" stroke="#65676b" stroke-width="1.4"/></svg></div>
</section>

<section class="card insights"><h3>Insights</h3><a href="#">See all</a></section>

<!-- right column -->
<section class="card create-post">
  <div class="mini-avatar">Pim</div>
  <div class="cp-field">Create Post</div>
  <div class="cp-actions">
    <span><svg width="16" height="14" viewBox="0 0 16 14"><rect width="16" height="14" rx="2" fill="#45bd62"/><polygon points="3,11 7,6 10,9 12,7 14,11" fill="#fff"/></svg>Photo/Video</span>
    <span><svg width="16" height="15" viewBox="0 0 16 15"><rect x="1" y="1" width="14" height="10" rx="2" fill="none" stroke="#65676b" stroke-width="1.5"/><polygon points="4,10.5 8,10.5 4,14" fill="#65676b"/></svg>Get Messages</span>
    <span><svg width="16" height="16" viewBox="0 0 16 16"><circle cx="8" cy="8" r="7" fill="none" stroke="#f7b928" stroke-width="1.6"/><path d="M5 9.5q3 3 6 0" fill="none" stroke="#f7b928" stroke-width="1.4"/></svg>Feeling/Activity</span>
  </div>
</section>

<section class="card create-bar">
  Create
  <span class="chip"><svg width="13" height="10" viewBox="0 0 13 10"><rect width="9" height="10" rx="2" fill="#1c1e21"/><polygon points="9,5 13,2 13,8" fill="#1c1e21"/></svg>Live</span>
  <span class="chip"><svg width="12" height="12" viewBox="0 0 12 12"><rect x=".8" y=".8" width="10.4" height="10.4" rx="1.5" fill="none" stroke="#1c1e21" stroke-width="1.4"/><line x1="1" y1="4" x2="11" y2="4" stroke="#1c1e21" stroke-width="1.4"/></svg>Event</span>
  <span class="chip"><svg width="12" height="11" viewBox="0 0 12 11"><rect y="2" width="12" height="9" rx="1.5" fill="#1c1e21"/><rect x="4" width="4" height="3" fill="none" stroke="#1c1e21" stroke-width="1.2"/></svg>Job</span>
  <span class="chip"><svg width="12" height="12" viewBox="0 0 12 12"><circle cx="6" cy="6" r="6" fill="#1c1e21"/><line x1="3.5" y1="8.5" x2="8.5" y2="3.5" stroke="#fff" stroke-width="1.3"/></svg>Offer</span>
  <span class="chip" style="font-weight:700">···</span>
</section>

<div class="abs section-label">PINNED POST</div>

<section class="card post">
  <div class="post-head"><div class="mini-avatar">Pim</div><div><b>Test2</b><small>1h · ●</small></div></div>
  <div class="abs" style="right:14px;top:12px;font-weight:700;color:#65676b">···</div>
  <div class="post-photo" role="img" aria-label="Studio portrait of the author lying beside her brindle rescue dog on a grey backdrop"></div>
  <div class="post-foot"><span>1</span><span style="margin-left:130px">0</span><span class="boost">Boost Unavailable</span></div>
</section>

<svg class="pointer" style="top:805px" viewBox="0 0 120 140"><polygon points="6,16 22,7 22,25" fill="var(--annot)"/><polygon points="46,16 62,7 62,25" fill="var(--annot)"/><polygon points="76,16 92,7 92,25" fill="var(--annot)"/><polyline points="92,16 110,16 110,100" fill="none" stroke="var(--annot)" stroke-width="1.6"/></svg>
<div class="callout photo">Professional<br>Image</div>

<div class="abs fab"></div>

</body>
</html>
```